Lorvex Tilo medical cannibis cultivation company

tag - Tilo rise
Lorvex Tilo medical cannabis cultivation - logo is selected- can we please see bold examples with our selection. We are mainly dealing with medical companies and professionals. We would like to be stand out in the crowd with our designs. Welcome any and all attempts. Thanks

Target Market(s)

Medical and Professional

Industry/Entity Type

Medical And Science

Font styles to use
Sans Serif

Colors

Designer to choose colors to be used in the design.

Requirements
Must have
• Bright colour and be bold- Love the teal and magenta that is currently on the dark background design.
Nice to have
• shading and the 3D affect- The shadowed appearance.
Should not have
• Anything related to illegal activity or un professional manners

```html
<!DOCTYPE html>
<html lang="en">
<head>
<meta charset="utf-8">
<title>Lorvex Tilo – Business Card</title>
<link rel="stylesheet" href="https://fonts.googleapis.com/css2?family=Roboto:wght@400;500;700&display=swap">
<style>
  :root {
    --magenta: #9e4d97;
    --teal: #00a8e1;
    --ink: #050506;
    --ring: #8a8f96;
    --white: #ffffff;
    --backdrop: #e8e8e8;
  }
  * { box-sizing: border-box; margin: 0; padding: 0; }
  html, body {
    width: 1125px; height: 1200px; overflow: hidden;
    background: var(--backdrop);
    font-family: "Roboto", Arial, sans-serif;
  }
  .card {
    position: absolute; left: 150px; width: 826px; height: 471px;
    border-radius: 24px; overflow: hidden; background: var(--magenta);
  }
  .card--front { top: 98px; }
  .card--back { top: 631px; }
  .card__art { position: absolute; inset: 0; width: 100%; height: 100%; }

  .holder { position: absolute; left: 54px; top: 50px; color: var(--white); }
  .holder__name { font-size: 29px; font-weight: 700; letter-spacing: 0.3px; }
  .holder__role { font-size: 19px; font-weight: 500; margin-top: 2px; }

  .brand {
    position: absolute; right: 52px; top: 96px; width: 230px;
    display: flex; flex-direction: column; align-items: center;
  }
  .brand__ring {
    width: 132px; height: 132px; border-radius: 50%;
    border: 4px solid var(--ring);
  }
  .brand__name {
    margin-top: 4px; font-size: 38px; font-weight: 500;
    color: var(--teal); letter-spacing: 0.5px; white-space: nowrap;
  }
  .brand__tag {
    display: flex; align-items: center; gap: 6px; width: 100%;
    font-size: 15px; letter-spacing: 2.5px; color: var(--ring);
  }
  .brand__tag::before, .brand__tag::after {
    content: ""; flex: 1; height: 1.5px; background: var(--ring);
  }

  .address {
    position: absolute; left: 54px; bottom: 34px;
    color: var(--white); font-size: 19px; line-height: 25px;
  }
  .address__web { letter-spacing: 1.6px; }

  .contacts {
    position: absolute; right: 52px; bottom: 34px;
    color: var(--white); font-size: 19px; list-style: none;
  }
  .contacts li {
    display: flex; justify-content: flex-end; align-items: center;
    gap: 12px; height: 26px;
  }
  .contacts svg { width: 20px; height: 20px; fill: var(--teal); }

  .back-brand {
    position: absolute; left: 0; right: 0; top: 104px;
    display: flex; flex-direction: column; align-items: center;
  }
  .back-brand__ring {
    width: 262px; height: 262px; border-radius: 50%;
    border: 7px solid var(--white);
  }
  .back-brand__name {
    margin-top: -150px; font-size: 36px; font-weight: 500;
    color: var(--white); letter-spacing: 1px;
  }
  .back-web {
    position: absolute; left: 0; right: 0; bottom: 42px; text-align: center;
    color: var(--white); font-size: 19px; letter-spacing: 5px;
  }
</style>
</head>
<body>

<section class="card card--front" aria-label="Card front">
  <svg class="card__art" viewBox="0 0 800 456" preserveAspectRatio="none" aria-hidden="true">
    <defs>
      <radialGradient id="leafShade" cx="0.5" cy="0.6" r="0.6">
        <stop offset="0" stop-color="#1a1420"/>
        <stop offset="1" stop-color="#050506"/>
      </radialGradient>
    </defs>
    <path d="M0,150 C60,152 130,190 185,246 C330,120 520,30 660,30 C740,30 785,80 800,118 L800,456 L0,456 Z" fill="#000"/>
    <path d="M30,154 C90,160 140,200 185,246 C330,120 520,30 660,30 C740,30 785,80 800,118 L800,128 C780,94 735,48 660,48 C530,48 350,140 185,262 C140,214 90,170 30,154 Z" fill="var(--teal)"/>
    <path d="M0,150 C60,152 130,190 185,262 C350,140 530,48 660,48 C735,48 780,94 800,128 L800,456 L0,456 Z" fill="url(#leafShade)"/>
    <circle cx="186" cy="188" r="20" fill="var(--teal)"/>
  </svg>
  <div class="card__art" role="img" aria-label="Faint leaf pattern over the dark area"></div>

  <div class="holder">
    <div class="holder__name">MARA HOLLEN</div>
    <div class="holder__role">CEO/FOUNDER</div>
  </div>

  <div class="brand">
    <div class="brand__ring"></div>
    <div class="brand__name">LORVEX TILO</div>
    <div class="brand__tag">TILO RISE</div>
  </div>

  <address class="address" style="font-style:normal">
    <div>2140 Birchwood Court</div>
    <div>Anchorage, Alaska 99508</div>
    <div class="address__web">www.lorvextilo.com</div>
  </address>

  <ul class="contacts">
    <li>555 214 3087
      <svg viewBox="0 0 24 24"><path d="M6.6 10.8a15 15 0 0 0 6.6 6.6l2.2-2.2c.3-.3.7-.4 1-.2 1.1.4 2.3.6 3.6.6.6 0 1 .4 1 1V20c0 .6-.4 1-1 1A17 17 0 0 1 3 4c0-.6.4-1 1-1h3.5c.6 0 1 .4 1 1 0 1.3.2 2.5.6 3.6.1.3 0 .7-.2 1z"/></svg>
    </li>
    <li>555 390 6721
      <svg viewBox="0 0 24 24"><path d="M7 1h10a2 2 0 0 1 2 2v18a2 2 0 0 1-2 2H7a2 2 0 0 1-2-2V3a2 2 0 0 1 2-2zm0 3v15h10V4zm5 16.2a1 1 0 1 0 0 .1z"/></svg>
    </li>
    <li>555 472 1958
      <svg viewBox="0 0 24 24"><path d="M6 2h10l2 2v5H6zM3 10h18a2 2 0 0 1 2 2v6h-4v4H5v-4H1v-6a2 2 0 0 1 2-2zm4 6v4h10v-4z"/></svg>
    </li>
    <li>mara@lorvextilo.com
      <svg viewBox="0 0 24 24"><path d="M2 5h20v14H2zm2 2v.5l8 5 8-5V7l-8 5z"/></svg>
    </li>
  </ul>
</section>

<section class="card card--back" aria-label="Card back">
  <div class="back-brand">
    <div class="back-brand__ring"></div>
    <div class="back-brand__name">LORVEX TILO</div>
  </div>
  <div class="back-web">www.lorvextilorise.com</div>
</section>

</body>
</html>
```